Website improvements and Adding Functionalities at https://mervo.site/tarnovex

1.Search functionality
2.Payment process functionality
3. Application configuration
4. Registration functionality activation
5. Chat functionality
6.Language switching functionality (Portuguese & French)
7.Bespoke interactive modules
8. Automated web scraping and data synchronisation mechanisms
9. News Page
10.Webinar facilities
11. Basic SEO optimisation
12. Speed and performance optimisation
13. Security configuration
14. Google Analytics integration
15. Cross-browser and mobile testing
16. Website deployment and launch support

Target Market(s)

My target markets are companies, investors, suppliers and professionals with an interest in the Mozambican oil and gas sector

Industry/Entity Type

Oil and Gas

Coding

Coded - Design and coding required

Number of Pages Required

1 page

Requirements
Must have
• Improve the existing page at https://mervo.site/tarnovex and add the following features to it: 1. Search functionality 2. Payment process functionality 3. Application configuration 4. Activation of registration functionality 5. Chat functionality 6. Language switching functionality (Portuguese & French) 7. Bespoke interactive modules 8. Automated web scraping and data synchronisation mechanisms 9. News Page

```html
<!DOCTYPE html>
<html lang="en">
<head>
<meta charset="utf-8">
<title>Tarnovex – Mozambique Oil &amp; Gas Intelligence</title>
<link href="https://fonts.googleapis.com/css2?family=Anton&family=Inter:wght@400;500;600;700&display=swap" rel="stylesheet">
<style>
:root{
  --navy:#1d1a3b;
  --navy-deep:#15132c;
  --orange:#e8501e;
  --orange-mid:#f26b21;
  --amber:#f8b135;
  --white:#ffffff;
  --ink:#1a1a2a;
  --grey:#444654;
  --head:'Anton',Impact,sans-serif;
  --body:'Inter',Arial,sans-serif;
}
*{margin:0;padding:0;box-sizing:border-box}
html,body{width:1200px;height:5089px;overflow:hidden}
body{position:relative;background:var(--white);font-family:var(--body);color:var(--ink)}
.abs{position:absolute}
.btn{position:absolute;display:flex;align-items:center;justify-content:center;font:700 12px var(--body);color:var(--white);border-radius:6px;text-transform:uppercase;letter-spacing:.2px}
.btn-grad{background:linear-gradient(90deg,var(--orange),var(--amber))}
.btn-dark{background:var(--navy)}
.h-title{font-family:var(--head);text-transform:uppercase;font-weight:400;line-height:1.15}
.rule{position:absolute;height:2px;background:rgba(248,177,53,.45)}
.rule::after{content:"";position:absolute;left:50%;top:-1px;width:38%;height:4px;transform:translateX(-50%);background:var(--amber)}
.rule.left::after{left:0;transform:none;width:28%}
.mark{position:absolute;width:34px;height:34px;border-radius:50%;background:var(--amber)}
.band{position:absolute;left:0;width:1200px}

/* header */
.site-header{top:0;left:0;width:1200px;height:137px;background:var(--white);border-bottom:3px solid var(--orange-mid)}
.top-strip{position:absolute;top:0;left:350px;width:850px;height:44px;background:var(--orange-mid);clip-path:polygon(0 0,100% 0,100% 100%,28px 100%)}
.brand{position:absolute;left:160px;top:18px;width:200px;text-align:center}
.brand-dot{display:block;width:56px;height:56px;margin:0 auto 8px;border-radius:50%;background:var(--navy)}
.brand-name{font:700 13px var(--body);letter-spacing:3px;color:var(--navy)}
.main-nav{position:absolute;left:410px;top:84px;display:flex;gap:24px;font:500 11px var(--body);color:var(--ink)}
.main-nav .active{color:var(--orange-mid)}
.circle-ico{position:absolute;width:28px;height:28px;border-radius:50%}

/* hero */
.hero{top:137px;height:600px;background:var(--navy);overflow:hidden}
.hero-photo{position:absolute;right:0;top:0;width:860px;height:600px;background:linear-gradient(90deg,var(--navy) 0%,rgba(29,26,59,0) 45%),linear-gradient(180deg,#4a4766 0%,#6e5a5a 45%,#b5782f 72%,#3a2b2a 100%)}
.hero h1{position:absolute;left:160px;top:70px;width:420px;font-size:32px;color:var(--white)}
.hero p{position:absolute;left:162px;top:200px;width:390px;font-size:12px;line-height:1.55;color:#e8e6f0}

/* text blocks */
.copy{position:absolute;font-size:14px;line-height:1.6;color:var(--grey)}
.photo-circle{position:absolute;border-radius:50%;border:8px solid var(--amber)}
.dark{background:linear-gradient(180deg,#2a2745,var(--navy-deep))}
.card{position:absolute;top:1552px;width:281px;height:352px;background:var(--white);border-radius:10px;text-align:center}
.card .ico{width:120px;height:120px;margin:32px auto 26px;border-radius:50%;background:var(--amber);display:flex;align-items:center;justify-content:center}
.card h3{font-family:var(--head);font-weight:400;font-size:18px;line-height:1.3;color:var(--navy);text-transform:uppercase;padding:0 20px}
.card .sep{width:24px;height:2px;background:var(--amber);margin:8px auto}
.card p{font-size:12px;line-height:1.55;color:var(--grey);padding:0 24px}
.why{position:absolute;top:2940px;width:320px;text-align:center;color:var(--white)}
.why .num{font-family:var(--head);font-size:98px;line-height:1;background:linear-gradient(180deg,var(--orange),var(--orange-mid));-webkit-background-clip:text;background-clip:text;color:transparent}
.why h3{font-family:var(--head);font-weight:400;font-size:21px;line-height:1.3;margin-top:14px}
.why p{font-size:11px;line-height:1.9;margin-top:12px;color:#d8d6e6}
.news-card{position:absolute;top:4231px;width:389px;height:248px;border-radius:12px;border:1px solid #c9c6d8;overflow:hidden}
.date{position:absolute;left:0;bottom:24px;padding:6px 28px 6px 14px;background:var(--amber);font-family:var(--head);font-size:12px;color:var(--navy);clip-path:polygon(0 0,100% 0,86% 100%,0 100%)}
.social{position:absolute;top:4994px;width:48px;height:48px;border-radius:50%}
</style>
</head>
<body>

<header class="abs site-header">
  <div class="top-strip"></div>
  <div class="brand"><span class="brand-dot"></span><div class="brand-name">TARNOVEX CO</div></div>
  <div class="btn btn-dark" style="left:775px;top:6px;width:128px;height:34px">Register Now</div>
  <div class="circle-ico" style="left:927px;top:10px;background:var(--navy)">
    <svg width="28" height="28" viewBox="0 0 28 28"><circle cx="13" cy="13" r="5" fill="none" stroke="#fff" stroke-width="2"/><line x1="16.5" y1="16.5" x2="20" y2="20" stroke="#fff" stroke-width="2"/></svg>
  </div>
  <div class="circle-ico" role="img" aria-label="French" style="left:965px;top:10px;border:2px solid #fff;background:linear-gradient(90deg,#1f3f9a 33%,#fff 33% 66%,#d3232a 66%)"></div>
  <div class="circle-ico" role="img" aria-label="Portuguese" style="left:1001px;top:10px;border:2px solid #fff;background:linear-gradient(90deg,#1f7a2e 42%,#d3232a 42%)"></div>
  <nav class="main-nav">
    <span class="active">Home</span><span>Industry Insights ▾</span><span>Oil and Gas Opportunities ▾</span><span>Supplier &amp; Company Network ▾</span><span>Legal Framework ▾</span>
  </nav>
</header>

<section class="band hero">
  <div class="hero-photo" role="img" aria-label="Offshore oil platform at sunset over the sea"></div>
  <h1 class="h-title">Access Mozambique’s Oil &amp; Gas Industry Intelligence in One Platform</h1>
  <p>Tarnovex is a modern online connection and consulting platform designed to facilitate access to the Mozambican Oil and Gas industry through premium industry insights, supplier information, tenders, legal frameworks, and strategic project data.</p>
  <div class="btn btn-grad" style="left:160px;top:292px;width:138px;height:38px">Register Now</div>
  <svg class="abs" style="left:166px;top:370px" width="90" height="22" viewBox="0 0 90 22"><path d="M11 4 4 11l7 7" stroke="#fff" stroke-width="2.5" fill="none"/><path d="M70 4l7 7-7 7" stroke="#f8b135" stroke-width="2.5" fill="none"/></svg>
  <svg class="abs" style="left:0;top:440px" width="1200" height="160" viewBox="0 0 1200 160" preserveAspectRatio="none">
    <polygon points="0,15 700,95 0,105" fill="#e8501e"/>
    <polygon points="0,95 760,100 0,150" fill="#f8b135"/>
    <polygon points="0,160 1200,160 1200,85 640,112 0,150" fill="#fff"/>
  </svg>
</section>

<section>
  <span class="mark" style="left:168px;top:795px"></span>
  <h2 class="h-title abs" style="left:160px;top:860px;font-size:38px;color:var(--navy)">What is Tarnovex?</h2>
  <div class="rule left" style="left:160px;top:918px;width:320px"></div>
  <p class="copy" style="left:160px;top:940px;width:420px">Tarnovex is a unique online platform built to connect businesses, investors, suppliers, and professionals with valuable information about the Mozambican Oil &amp; Gas sector.<br><br>Through a secure digital paywall system, users gain access to organized, up-to-date, and carefully selected industry information that supports better decision-making, market understanding, and business opportunities within Mozambique’s growing hydrocarbons industry.</p>
  <div class="btn btn-grad" style="left:160px;top:1210px;width:140px;height:40px">Learn More</div>
  <div class="photo-circle" role="img" aria-label="Oil refinery and pipelines at sunset" style="left:656px;top:836px;width:394px;height:394px;background:linear-gradient(180deg,#d4692a,#8a3e25 60%,#2c1e2a)"></div>
</section>

<section class="band dark" style="top:1344px;height:780px">
  <div class="abs" style="inset:0;background:linear-gradient(180deg,rgba(70,62,80,.35),rgba(20,18,40,.2))" role="img" aria-label="Oil rigs at dusk in the background"></div>
  <span class="mark" style="left:583px;top:38px"></span>
  <h2 class="h-title abs" style="left:0;width:1200px;text-align:center;top:100px;font-size:40px;color:var(--white)">What You Will Access</h2>
  <div class="rule" style="left:450px;top:170px;width:300px"></div>
  <svg class="abs" style="left:74px;top:340px" width="1040" height="30" viewBox="0 0 1040 30"><path d="M18 4 8 15l10 11" stroke="#fff" stroke-width="3" fill="none"/><path d="M1024 4l10 11-10 11" stroke="#f8b135" stroke-width="3" fill="none"/></svg>
  <svg class="abs" style="left:0;top:600px" width="1200" height="180" viewBox="0 0 1200 180" preserveAspectRatio="none">
    <polygon points="0,0 700,80 0,140" fill="#e8501e"/>
    <polygon points="0,80 1200,40 0,180" fill="#f8b135"/>
    <polygon points="0,180 1200,180 1200,60 620,170" fill="#fff"/>
  </svg>
</section>

<div class="card" style="left:160px">
  <div class="ico"><svg width="40" height="50" viewBox="0 0 40 50"><rect x="6" y="4" width="28" height="42" rx="5" fill="#e8501e"/><rect x="6" y="16" width="28" height="3" fill="#fff"/><rect x="6" y="31" width="28" height="3" fill="#fff"/></svg></div>
  <h3>Hydrocarbon Industry Information</h3><div class="sep"></div>
  <p>General information and insights about Mozambique’s oil and gas sector.</p>
</div>
<div class="card" style="left:459px">
  <div class="ico"><svg width="52" height="52" viewBox="0 0 52 52"><circle cx="26" cy="26" r="18" fill="#e8501e"/><circle cx="26" cy="26" r="8" fill="#f8b135"/><path d="M26 2v8M26 42v8M2 26h8M42 26h8M9 9l6 6M37 37l6 6M43 9l-6 6M15 37l-6 6" stroke="#e8501e" stroke-width="5"/></svg></div>
  <h3>Main Gas Projects</h3><div class="sep"></div>
  <p>Details about major gas and energy projects operating in Mozambique.</p>
</div>
<div class="card" style="left:757px">
  <div class="ico"><svg width="46" height="46" viewBox="0 0 46 46"><rect x="3" y="4" width="40" height="10" rx="2" fill="#e8501e"/><rect x="3" y="18" width="40" height="10" rx="2" fill="#e8501e"/><rect x="3" y="32" width="40" height="10" rx="2" fill="#e8501e"/><rect x="8" y="8" width="12" height="2" fill="#fff"/><rect x="8" y="22" width="12" height="2" fill="#fff"/><rect x="8" y="36" width="12" height="2" fill="#fff"/></svg></div>
  <h3>Supplier &amp; Company Database</h3><div class="sep"></div>
  <p>Mozambican companies capable of meeting Level 3 supply requirements.</p>
</div>

<section>
  <span class="mark" style="left:168px;top:2175px"></span>
  <h2 class="h-title abs" style="left:160px;top:2238px;width:380px;font-size:40px;color:var(--navy)">How the Platform Works</h2>
  <div class="rule left" style="left:160px;top:2356px;width:426px"></div>
  <p class="copy" style="left:160px;top:2382px;width:420px">The platform operates through a secure automated payment system that grants registered users access to premium and exclusive content. By subscribing, users receive organized industry intelligence designed to save time, improve market access, and support strategic business growth within Mozambique’s energy sector.</p>
  <div class="btn btn-grad" style="left:160px;top:2538px;width:138px;height:40px">Learn More</div>
  <div class="photo-circle" role="img" aria-label="Warehouse workers checking shipment boxes" style="left:650px;top:2165px;width:392px;height:392px;background:linear-gradient(160deg,#c9b9a3,#7d6a58 55%,#3a3240)"></div>
</section>

<section class="band dark" style="top:2728px;height:780px">
  <div class="abs" style="inset:0;background:linear-gradient(90deg,rgba(40,36,62,.2),rgba(80,72,96,.35))" role="img" aria-label="Worker in hard hat silhouetted against an industrial site"></div>
  <span class="mark" style="left:583px;top:40px"></span>
  <h2 class="h-title abs" style="left:0;width:1200px;text-align:center;top:98px;font-size:40px;color:var(--white)">Why Tarnovex Is Unique</h2>
  <div class="rule" style="left:455px;top:170px;width:290px"></div>
  <svg class="abs" style="left:586px;top:573px" width="28" height="46" viewBox="0 0 28 46"><path d="M14 2v38M4 30l10 10 10-10" stroke="#f8b135" stroke-width="3" fill="none"/></svg>
  <svg class="abs" style="left:0;top:610px" width="1200" height="170" viewBox="0 0 1200 170" preserveAspectRatio="none">
    <polygon points="0,0 700,90 0,130" fill="#e8501e"/>
    <polygon points="0,80 1200,60 0,170" fill="#f8b135"/>
    <polygon points="0,170 1200,170 1200,80 620,170" fill="#fff"/>
  </svg>
</section>

<div class="why" style="left:128px"><div class="num">01</div><h3>Up-to-Date Industry<br>Intelligence</h3><p>Receive frequent updates about developments<br>in Mozambique’s Oil &amp; Gas sector.</p></div>
<div class="why" style="left:440px"><div class="num">02</div><h3>High-Quality Curated<br>Information</h3><p>Access carefully selected and synthesized<br>information tailored to industry stakeholders.</p></div>
<div class="why" style="left:736px"><div class="num">03</div><h3>Time-Saving<br>Access</h3><p>Avoid spending hours searching through<br>scattered online sources with organized and<br>accessible content in one platform.</p></div>

<section>
  <span class="mark" style="left:583px;top:3580px"></span>
  <h2 class="h-title abs" style="left:0;width:1200px;text-align:center;top:3640px;font-size:44px;line-height:1.18;color:var(--navy)">Start Exploring Mozambique’s Oil &amp; Gas<br>Opportunities</h2>
  <div class="rule" style="left:400px;top:3758px;width:400px"></div>
  <p class="copy" style="left:170px;width:860px;top:3790px;text-align:center">Register today to access premium industry information, supplier networks, tenders, and strategic market<br>insights through Tarnovex.</p>
  <div class="btn btn-grad" style="left:454px;top:3872px;width:140px;height:40px">Register Now</div>
  <div class="btn btn-dark" style="left:605px;top:3872px;width:140px;height:40px">Contact Us</div>
</section>

<section class="band dark" style="top:4013px;height:700px">
  <span class="mark" style="left:583px;top:45px"></span>
  <h2 class="h-title abs" style="left:0;width:1200px;text-align:center;top:108px;font-size:40px;color:var(--white)">Latest News</h2>
  <div class="rule" style="left:487px;top:178px;width:256px"></div>
  <svg class="abs" style="left:0;top:560px" width="1200" height="160" viewBox="0 0 1200 160" preserveAspectRatio="none">
    <polygon points="0,0 700,90 0,120" fill="#e8501e"/>
    <polygon points="0,80 1200,30 0,150" fill="#f8b135"/>
    <polygon points="0,160 1200,160 1200,40 0,150" fill="#fff"/>
  </svg>
</section>

<article class="news-card" style="left:194px;background:linear-gradient(180deg,#2e2b45,#1d1a35)">
  <h3 class="h-title" style="color:var(--white);font-size:22px;text-align:center;padding:38px 30px 0">Lorem ipsum dolor sit amet, consectetur adipiscing</h3>
  <p style="color:#f2f0f8;font-size:14px;line-height:1.55;text-align:center;padding:8px 30px 0">Lorem ipsum dolor sit amet, consectetur adipiscing elit, sed do eiusmod tempor incididunt ut labore et dolore magna aliqua.</p>
  <div class="date">01 JUN 2026</div>
</article>
<article class="news-card" style="left:615px;background:linear-gradient(160deg,#8fa7c3,#5d6e84 55%,#2f3545)" role="img" aria-label="Two engineers in hard hats reviewing a tablet at a plant">
  <div class="date">01 JUN 2026</div>
</article>
<h3 class="h-title abs" style="left:615px;width:389px;top:4508px;text-align:center;font-size:22px;color:var(--white)">Sed do eiusmod tempor incididunt<br>ut labore et dolore</h3>

<footer>
  <div class="abs" style="left:0;width:1200px;top:4780px;text-align:center">
    <span style="display:block;width:110px;height:110px;margin:0 auto 22px;border-radius:50%;background:var(--navy)"></span>
    <div style="font:700 17px var(--body);letter-spacing:5px;color:var(--navy)">TARNOVEX CO</div>
  </div>
  <span class="social" role="img" aria-label="Social profile" style="left:516px;background:var(--orange)"></span>
  <span class="social" role="img" aria-label="Social profile" style="left:576px;background:var(--navy)"></span>
  <span class="social" role="img" aria-label="Social profile" style="left:636px;background:var(--navy)"></span>
  <p class="abs" style="left:0;width:1200px;top:5062px;text-align:center;font:600 11px var(--body);color:var(--navy)">© 2026 by Tarnovex Co. All Rights Reserved.</p>
  <div class="abs" style="left:963px;top:5031px;width:164px;height:58px;background:var(--amber);border-radius:8px 8px 0 0;display:flex;justify-content:center;padding-top:16px;font:400 17px var(--head);color:var(--navy)">CHAT WITH US</div>
  <span class="abs" style="left:1154px;top:5056px;font:700 11px var(--body);color:var(--navy)">M1</span>
</footer>

</body>
</html>
```